holloway paving service

Needs to have phone number 0418259730 and email markholloway@brightmail.com.au.
ABN 62318470915
name mark holloway

For all your concreting solutions
Excavation
Exposed & colour concrete
House & shed slabs
Driveways
Landing & steps

Contact Information for Business Card

ph 0418259730
email markholloway@brightmail.com.au.
ABN 62318470915
name mark holloway

```html
<!DOCTYPE html>
<html lang="en">
<head>
<meta charset="utf-8">
<title>Holloway Paving Service – Business Card</title>
<link rel="stylesheet" href="https://fonts.googleapis.com/css2?family=Montserrat:wght@500;600;700&family=Lato:wght@400;700&display=swap">
<style>
  :root {
    --orange: #f26a21;
    --grey: #5f5f60;
    --grey-dark: #4a4a4b;
    --rule: #d4d4d4;
    --white: #ffffff;
    --text: #3d3d3d;
    --backdrop: #2e2a28;
  }
  * { box-sizing: border-box; margin: 0; padding: 0; }
  html, body {
    width: 1200px; height: 844px; overflow: hidden;
    background: var(--backdrop);
    font-family: "Lato", sans-serif;
  }
  .card {
    position: absolute; top: 279px;
    width: 500px; height: 286px; overflow: hidden;
  }

  /* Front */
  .card--front { left: 60px; background: var(--white); }
  .brand {
    position: absolute; top: 34px; left: 160px;
    display: flex; align-items: center; gap: 12px;
  }
  .brand__square { width: 34px; height: 34px; background: var(--orange); }
  .brand__divider { width: 1.5px; height: 50px; background: var(--orange); }
  .brand__text { font-family: "Montserrat", sans-serif; line-height: 1.1; }
  .brand__name { color: var(--orange); font-weight: 600; font-size: 14px; letter-spacing: .5px; }
  .brand__sub {
    color: var(--grey); font-weight: 500; font-size: 10px; letter-spacing: 2px;
    display: flex; align-items: center; gap: 5px;
  }
  .brand__sub::before, .brand__sub::after { content: ""; height: 1px; width: 22px; background: var(--grey); }
  .brand__phone { color: var(--orange); font-weight: 500; font-size: 11px; letter-spacing: 1.2px; }
  .rule { position: absolute; left: 100px; right: 0; height: 1px; background: var(--rule); }
  .rule--one { top: 112px; }
  .rule--two { top: 138px; left: 60px; }
  .person {
    position: absolute; left: 40px; top: 160px;
    font-family: "Montserrat", sans-serif; font-weight: 700; font-size: 16px; letter-spacing: .5px;
    color: var(--grey);
  }
  .person__first { color: var(--orange); }
  .contact { position: absolute; left: 40px; top: 190px; font-size: 12.5px; color: var(--text); }
  .contact__label { color: var(--orange); font-weight: 700; }
  .rule--three { top: 212px; left: 40px; width: 180px; }
  .tagline {
    position: absolute; left: 40px; top: 220px;
    font-family: "Montserrat", sans-serif; font-weight: 600; font-size: 11px; color: var(--orange);
  }
  .services { position: absolute; left: 40px; top: 238px; font-size: 12px; line-height: 1.45; color: var(--text); }

  /* Back */
  .card--back { left: 640px; background: var(--orange); }
  .back__panel { position: absolute; inset: 0; }
  .back__brand {
    position: absolute; top: 110px; left: 225px;
    display: flex; align-items: center; gap: 12px;
    font-family: "Montserrat", sans-serif; color: var(--white); line-height: 1.15;
  }
  .back__square { width: 34px; height: 34px; background: var(--white); }
  .back__name { font-weight: 600; font-size: 15px; letter-spacing: .5px; }
  .back__sub { font-weight: 500; font-size: 10.5px; letter-spacing: 2px; display: flex; align-items: center; gap: 6px; }
  .back__sub::before, .back__sub::after { content: ""; height: 1px; width: 40px; background: var(--white); }
  .back__phone { font-weight: 500; font-size: 11px; letter-spacing: 1.5px; padding-left: 60px; }
</style>
</head>
<body>
  <section class="card card--front">
    <div class="brand">
      <div class="brand__square"></div>
      <div class="brand__divider"></div>
      <div class="brand__text">
        <div class="brand__name">HOLLOWAY PAVING</div>
        <div class="brand__sub">SERVICE</div>
        <div class="brand__phone">0418259730</div>
      </div>
    </div>
    <div class="rule rule--one"></div>
    <div class="rule rule--two"></div>
    <div class="person"><span class="person__first">MARK</span> HOLLOWAY</div>
    <div class="contact"><span class="contact__label">P:</span> 0418259730 | <span class="contact__label">E:</span> markholloway@brightmail.com.au</div>
    <div class="rule rule--three"></div>
    <div class="tagline">FOR ALL YOUR CONCRETING SOLUTIONS</div>
    <div class="services">
      Excavation &nbsp;| &nbsp;Exposed &amp; colour concrete<br>
      House &amp; shed slabs | Driveways | Landing &amp; steps
    </div>
  </section>

  <section class="card card--back">
    <svg class="back__panel" viewBox="0 0 500 286" aria-hidden="true">
      <polygon points="0,0 130,0 200,286 0,286" fill="var(--grey)"/>
    </svg>
    <div class="back__brand">
      <div class="back__square"></div>
      <div>
        <div class="back__name">HOLLOWAY PAVING</div>
        <div class="back__sub">SERVICE</div>
        <div class="back__phone">0418259730</div>
      </div>
    </div>
  </section>
</body>
</html>
```